Business Cards for IT Consulting Company (Managed Service Provider)

I am looking to have some business cards printed and would like some designs. We are an IT Consulting company based in Vancouver BC. I would like a nice clean and modern look to the cards. I have uploaded all the versions of my logo so parts can be used as needed. Here is a snippit from our website homepage:

Quillbrook Networks Ltd. is an IT Solutions Partner located in Vancouver BC, Canada. We offer IT solutions and support to customers in the greater Vancouver Area. With expertise in Microsoft platforms, as well as Linux and Mac OSX and over 12 years experience in the IT industry, Quillbrook Networks is dedicated to offering our clients top quality service and products. We take pride in the solutions we offer our customers. The greatest compliment a client can give us is to recommend our services.

Quillbrook Networks Ltd. offers a wide range of IT services from onsite service to remote support and managed service solutions. This allows clients to choose the support path that best suits their company’s needs. Supporting many different sized companies from small to enterprise level over the past 12 years Quillbrook Networks has the experience and expertise needed to ensure things run smoothly. Allowing our clients to focus on doing business.

Revolutionizing the way IT services are delivered.

Quillbrook Networks is dedicated to providing our clients with IT solutions that work and grow with them for years to come. This philosophy helps save money in the long run instead of replacing equipment constantly. Far too often IT solutions are not well thought out and while possibly solving the problem at hand, require replacement due to growth or quality within a very short time frame. Quillbrook Networks takes pride in providing solutions that will last and be able to accommodate growth without the need for replacement.

Industry/Entity Type

Information Technology

Contact Information for Business Card

Quillbrook Networks Ltd.
(Employee Name)
Eml: (Employees Email Address)
Web: quillbrook.me
Ph: 604-555-0148

Font styles to use
Serif
Sans Serif

Requirements
Must have
• The Company logo and company colors.
Nice to have
• - Our tag line: "Revolutionizing IT Services" or "Revolutionizing the way IT services are delivered."
• - Also I really like the idea of nature and technology together blending which is sort of where my logo came from so integrating that somehow onto the business cards would be great.

```html
<!DOCTYPE html>
<html lang="en">
<head>
<meta charset="utf-8">
<title>Quillbrook Networks Ltd. — Business Card</title>
<link href="https://fonts.googleapis.com/css2?family=Raleway:wght@300;400;500;700&display=swap" rel="stylesheet">
<style>
  :root {
    --bg: #bfe3d8;
    --card: #ffffff;
    --brand-blue: #00a9e0;
    --ink: #2f2f2f;
    --grey: #5a5a5a;
    --white: #ffffff;
  }
  * { box-sizing: border-box; margin: 0; padding: 0; }
  html, body { width: 1200px; height: 856px; overflow: hidden; }
  body {
    background: var(--bg);
    font-family: "Raleway", Arial, sans-serif;
    position: relative;
  }
  .card {
    position: absolute;
    width: 620px;
    height: 354px;
    background: var(--card);
    border-radius: 30px;
    overflow: hidden;
    box-shadow: 0 10px 30px rgba(0, 60, 50, 0.18);
  }

  /* Back of card */
  .card-back { left: 520px; top: 60px; }
  .card-back .brand {
    position: absolute;
    left: 0; right: 0; top: 110px;
    display: flex; align-items: center; justify-content: center; gap: 18px;
  }
  .brand-mark {
    width: 44px; height: 44px;
    border: 4px solid var(--brand-blue);
    border-radius: 50%;
    flex: none;
  }
  .brand-name {
    color: var(--brand-blue);
    font-weight: 700;
    line-height: 1.05;
  }
  .card-back .brand-name { font-size: 42px; }
  .card-back .website {
    position: absolute;
    left: 0; right: 0; top: 238px;
    text-align: center;
    font-size: 26px;
    font-weight: 400;
    color: var(--grey);
    letter-spacing: 0.5px;
  }
  .card-back .website .domain { color: var(--brand-blue); }

  /* Front of card */
  .card-front { left: 60px; top: 442px; }
  .card-front .brand {
    position: absolute;
    left: 30px; top: 134px;
    width: 220px;
    display: flex; align-items: center; gap: 12px;
  }
  .card-front .brand-mark { width: 28px; height: 28px; border-width: 3px; }
  .card-front .brand-name { font-size: 22px; }
  .card-front .brand-name span { display: block; }

  .contact-panel {
    position: absolute;
    left: 262px; right: 0; top: 0;
    height: 272px;
    background: var(--brand-blue);
    border-top-right-radius: 30px;
    padding: 44px 0 0 40px;
    color: var(--white);
  }
  .person-name {
    font-size: 34px;
    font-weight: 300;
    letter-spacing: 1px;
    margin-bottom: 18px;
  }
  .contact-list { list-style: none; }
  .contact-list li {
    display: flex; align-items: center; gap: 14px;
    font-size: 19px; font-weight: 400;
    height: 36px;
  }
  .contact-list .icon {
    width: 26px; height: 26px; flex: none;
    background: var(--white);
    border-radius: 50%;
    display: flex; align-items: center; justify-content: center;
  }
  .contact-list .icon svg { width: 16px; height: 16px; }

  .tagline-strip {
    position: absolute;
    left: 262px; right: 0; top: 272px;
    height: 42px;
    display: flex; align-items: center; justify-content: flex-end;
    padding-right: 24px;
    font-size: 24px; font-weight: 400;
    white-space: nowrap;
  }
  .tagline-strip .lead { color: var(--brand-blue); }
  .tagline-strip .rest { color: var(--ink); margin-left: 7px; }
  .base-band {
    position: absolute;
    left: 262px; right: 0; bottom: 0;
    height: 40px;
    background: var(--brand-blue);
  }
</style>
</head>
<body>

  <section class="card card-back" aria-label="Business card, back">
    <div class="brand">
      <span class="brand-mark" aria-hidden="true"></span>
      <span class="brand-name">Quillbrook Networks Ltd.</span>
    </div>
    <p class="website">www.<span class="domain">quillbrook</span>.me</p>
  </section>

  <section class="card card-front" aria-label="Business card, front">
    <div class="brand">
      <span class="brand-mark" aria-hidden="true"></span>
      <span class="brand-name"><span>Quillbrook</span><span>Networks</span></span>
    </div>

    <div class="contact-panel">
      <h1 class="person-name">DANIEL HART</h1>
      <ul class="contact-list">
        <li>
          <span class="icon" aria-hidden="true">
            <svg viewBox="0 0 16 16"><path fill="#00a9e0" d="M3.2 1.5l2.4 2.6-1.3 1.6c.8 1.9 2.3 3.4 4.2 4.3l1.6-1.3 2.6 2.4-1.3 2.2C6.6 13.2 2.8 9.4 1 4.6z"/></svg>
          </span>
          daniel.hart@quillbrook.me
        </li>
        <li>
          <span class="icon" aria-hidden="true">
            <svg viewBox="0 0 16 16"><rect x="2" y="4" width="12" height="8" fill="none" stroke="#00a9e0" stroke-width="1.6"/><path d="M2 4l6 5 6-5" fill="none" stroke="#00a9e0" stroke-width="1.6"/></svg>
          </span>
          quillbrook.me
        </li>
        <li>
          <span class="icon" aria-hidden="true">
            <svg viewBox="0 0 16 16"><g fill="none" stroke="#00a9e0" stroke-width="1.4"><circle cx="8" cy="8" r="6"/><ellipse cx="8" cy="8" rx="2.6" ry="6"/><path d="M2 8h12M3 5h10M3 11h10"/></g></svg>
          </span>
          604-555-0148
        </li>
      </ul>
    </div>

    <p class="tagline-strip"><span class="lead">Revolutionizing</span><span class="rest">IT Services</span></p>
    <div class="base-band"></div>
  </section>

</body>
</html>
```